Attorney Website Home Page Design Project

I am starting my law firm and I need a website design. I am going to be practicing in the field of personal injury, and I need a website design that conveys reliability and professionalism, but is still personable. This website will mostly be accessed by potential clients looking for information about me, and my potential clients are individual people, not businesses.

I have a logo that I just had designed by a designer on this site that I will be using. The colors used int he site should be complementary to the ones in that logo. Also, I have listed three websites that I want to base the overall look of my site on. This does NOT mean I want to copy them- instead, I am listing them for inspiration and to better convey what I am looking for.

Please use filler text and filler images for everything, and structure the menus as I have described below.

I will be taking this design- as a PSD file- and having it converted in to HTML, so I will need a perfect, multi-layered PSD file when completed.

I also will need a contact form that is consistent on every page.

Overall design on this site is up to you. See the attached logo files for inspiration on the color scheme. I am looking for a professional but personal website for my law firm. Check out the sites below for inspiration.

I. Websites for inspiration:

www.DonovanKemptLaw.com THIS IS WHERE I WANT ABOUT 50% OF YOUR INSPIRATION TO COME FROM

www.OkaforPersonalInjury.com 25%

www.VelmorAdvocate.com 25%

I want all aspects of this site- menu panels and what not to be expandable and done in full uncompressed photoshop psd format so I can have them converted to html, and then in to a full site.

See the attached logo- the colors in it should direct the overall color scheme of the site.

I want you to use placeholder text and placeholder images- you can use white boxes with text in them that says what type of image should be used in its place. I also want a placeholder for a video on the home page.

II. Menu structure:

A. Main Menu and Submenu Items:

Our Purpose

What An Attorney Does

Why Choose Quillbrook Attorneys

No Fee Guarantee

Cases We Handle (Below is a partial list- take the whole list from DonovanKemptLaw.com

Auto Accidents

Slip and Fall Injuries

Dog Bites

Animal Bites

General Injury Cases

Your Case

How Are You Feeling?

What You Should Be Doing

Talk To Us

Contact Us

Target Market(s)

Injured people who need an attorney. Individuals, not companies.

Industry/Entity Type

Law Firm

Requirements
Must have
• Must be themed according to the websites I have listed and in line with my logo.

Must convey reliability, professionalism and warmth.

Must appeal to an individual person- I am practicing personal injury, not corporate or business law.

Must have one eye-catching item- "Contact Us Now to Get These Questions Answered:" with a 10 item numbered list of questions.
Should not have
• The site should not be cluttered or difficult to follow.

It should not be elitist or look like it is designed for corporate law.

```html
<!DOCTYPE html>
<html lang="en">
<head>
<meta charset="utf-8">
<title>Quillbrook Attorneys</title>
<link rel="stylesheet" href="https://fonts.googleapis.com/css2?family=Source+Sans+3:wght@400;600;700&family=PT+Serif:wght@700&family=Arimo:wght@400;700&display=swap">
<style>
:root{
  --navy:#0b4a82;
  --blue-link:#1a6fb0;
  --sky:#1aa0d8;
  --red:#c8161d;
  --orange:#e0662a;
  --text:#333;
  --line:#dcdcdc;
  --footer:#323232;
  --footer-text:#d8d8d8;
  --white:#fff;
}
*{box-sizing:border-box;margin:0;padding:0}
html,body{width:890px;height:1200px;overflow:hidden;background:var(--white)}
body{font-family:"Arimo",Arial,sans-serif;color:var(--text)}
.page{position:relative;width:890px;height:1200px;overflow:hidden}
.abs{position:absolute}

/* brand wordmark */
.brand-name{font-family:"Source Sans 3",sans-serif;font-weight:700;color:var(--navy);text-transform:uppercase;white-space:nowrap}
.brand-name .main{display:block;font-size:40px;line-height:38px;letter-spacing:1px}
.brand-name .sub{display:flex;align-items:center;gap:8px;font-size:11px;line-height:14px;letter-spacing:5px;margin-top:3px}
.brand-name .sub::before,.brand-name .sub::after{content:"";flex:1;height:1px;background:currentColor;opacity:.6}

/* header */
.brand{left:146px;top:8px;width:326px}
.callout{left:476px;top:0;width:271px;height:71px;background:linear-gradient(#f4f4f4,#d9d9d9);border:1px solid #c4c4c4;border-top:0;text-align:center}
.callout-lead{font-family:"PT Serif",serif;font-weight:700;font-size:15px;color:#333;margin-top:4px}
.callout-phone{font-family:"PT Serif",serif;font-weight:700;font-size:36px;line-height:40px;color:var(--navy)}
.callout-phone .area{color:var(--red);font-size:28px}

/* hero */
.hero{left:0;top:74px;width:890px;height:461px;background:repeating-linear-gradient(45deg,#e8eaec 0 2px,#e1e3e5 2px 4px)}
.hero-photo{left:154px;top:0;width:374px;height:461px;background:linear-gradient(#e1e3e5 0%,#d8b597 25%,#cfa284 55%,#e8e8e8 70%,#23242b 85%)}
.nav{left:379px;top:12px;width:373px;height:34px;background:linear-gradient(#1663a8,#07457e);border-radius:4px;display:flex;align-items:center;padding-left:8px;white-space:nowrap}
.nav a{flex:none;font-family:"Source Sans 3",sans-serif;font-size:11px;color:var(--white);text-decoration:none;padding:0 8px;border-right:1px solid rgba(255,255,255,.2);line-height:24px}
.nav .lang{flex:none;display:flex;align-items:center;gap:6px;margin-left:6px;background:rgba(0,0,0,.2);border-radius:3px;padding:0 6px;height:22px;font-family:"Source Sans 3",sans-serif;font-size:11px;color:var(--white)}
.lang .flag{width:18px;height:11px;background:linear-gradient(#c8161d 50%,#f2f2f2 50%);background-size:100% 3px}
.contact{left:535px;top:81px;width:219px;height:307px;background:#b9bfc5;border-radius:4px;padding:7px}
.contact-inner{width:100%;height:100%;background:linear-gradient(160deg,#1a66ab,#063868);border-radius:3px;padding:8px 22px 0}
.contact h2{font-family:"Source Sans 3",sans-serif;font-weight:600;font-size:19px;line-height:26px;color:var(--white);text-align:center}
.contact h2 .free{color:#f0c85a}
.field{background:var(--white);border-radius:3px;height:22px;margin-top:7px;font-size:7px;color:#999;padding:6px 7px}
.field.area{height:93px}
.contact .send{margin-top:11px;height:20px;border-radius:4px;background:linear-gradient(#fff,#c9c9c9);font-family:"Source Sans 3",sans-serif;font-weight:700;font-size:15px;line-height:20px;color:#333;text-align:center}

/* columns */
.col h2{font-family:"Source Sans 3",sans-serif;font-weight:400;font-size:19px;line-height:26px;color:#333}
.col h2.alert{color:var(--red)}
.welcome{left:146px;top:555px;width:182px}
.welcome-photo{margin-top:12px;width:182px;height:69px;border:3px solid #eee;background:linear-gradient(100deg,#6b4a30,#b48a5a 50%,#3e2a1c)}
.body-copy{font-size:8.6px;line-height:14.7px;color:#444;margin-top:6px}
.btn{display:inline-block;background:linear-gradient(#1f6fb3,#0b4a82);color:var(--white);font-family:"Source Sans 3",sans-serif;font-weight:600;font-size:10px;border-radius:3px;padding:0 7px;line-height:20px}
.practice{left:349px;top:555px;width:191px}
.p-list{margin-top:10px}
.p-item{position:relative;height:67px;border-bottom:1px solid var(--line);padding-left:69px}
.p-item+.p-item{padding-top:8px}
.p-item:last-child{border-bottom:0}
.p-item .thumb{position:absolute;left:0;top:0;width:57px;height:52px;border:2px solid #eee}
.p-item+.p-item .thumb{top:8px}
.p-item h3{font-family:"Source Sans 3",sans-serif;font-weight:400;font-size:11px;color:var(--blue-link)}
.p-item p{font-size:8.6px;line-height:13px;color:#444}
.questions{left:553px;top:555px;width:191px}
.q-item{position:relative;height:67px;padding-left:70px}
.q-item .video{position:absolute;left:0;top:0;width:63px;height:53px;background:linear-gradient(#cfd2d6 0 60%,#2a2c31 60%);border:1px solid #999}
.q-item h3{font-size:8.6px;line-height:14px;font-weight:400;color:var(--red)}
.q-item p{font-size:8.6px;line-height:13px;color:#444}
.q-item .more{position:absolute;right:0;bottom:3px;font-size:8px;font-style:italic;color:var(--red)}

/* info strip */
.info{left:146px;top:833px;width:598px;height:99px;border:1px solid var(--line);border-radius:4px;background:linear-gradient(#fff,#f4f4f4);display:flex}
.info section{flex:1;padding:7px 17px 0;position:relative}
.info section+section{border-left:1px solid #e6e6e6}
.info h3{font-family:"Source Sans 3",sans-serif;font-weight:400;font-size:15px;color:#333}
.info h3.lead{color:var(--sky)}
.info p{font-size:7.8px;line-height:11.5px;text-align:justify;margin-top:6px}
.info .read{position:absolute;right:25px;top:83px;font-size:8px;color:var(--orange)}

/* footer */
.footer{left:0;top:950px;width:890px;height:250px;background:var(--footer);color:var(--footer-text)}
.footer h2{font-family:"Source Sans 3",sans-serif;font-weight:400;font-size:15px;color:var(--white)}
.member{left:146px;top:26px;width:240px}
.member .arrows{position:absolute;right:0;top:2px}
.m-item{position:relative;padding-left:60px;margin-top:10px;height:70px}
.m-item+.m-item{margin-top:12px}
.m-item .badge{position:absolute;left:0;top:2px;width:48px;height:45px;background:#7a1a12;border:2px solid #e8e0d0}
.m-item p{font-size:8.6px;line-height:14px;text-align:justify}
.m-item .btn{position:absolute;right:0;top:49px}
.office{left:427px;top:26px;width:150px;font-size:8.4px;line-height:16px}
.office .brand-name{color:#aaa;margin-top:6px;width:150px}
.office .brand-name .main{font-size:21px;line-height:22px;letter-spacing:.5px}
.office .brand-name .sub{font-size:6px;line-height:8px;letter-spacing:3px;margin-top:1px}
.office .row{display:flex;justify-content:space-between}
.office a{color:#5ab2ea;text-decoration:none}
.office h3{color:var(--white);font-size:10px;margin-top:8px}
.connect{left:612px;top:26px}
.connect ul{list-style:none;margin-top:8px}
.connect li{display:flex;align-items:center;gap:17px;height:29px;font-size:9.5px}
.connect .sq{width:24px;height:24px;border-radius:3px;background:#6f8fb0}
.copyright{right:116px;top:216px;text-align:right;font-size:8px;line-height:13px;color:#aaa}
</style>
</head>
<body>
<div class="page">

  <header>
    <div class="abs brand">
      <div class="brand-name"><span class="main">Quillbrook</span><span class="sub">Attorneys</span></div>
    </div>
    <div class="abs callout">
      <div class="callout-lead">CALL for a FREE CONSULTATION</div>
      <div class="callout-phone"><span class="area">(800)</span>555-0187</div>
    </div>
  </header>

  <section class="abs hero">
    <div class="abs hero-photo" role="img" aria-label="Portrait of a smiling attorney in a dark suit"></div>
    <nav class="abs nav">
      <a href="#">Our Story</a><a href="#">Your Stories</a><a href="#">Our Services</a><a href="#">Your Case</a>
      <span class="lang"><span class="flag"></span>English
        <svg width="8" height="6" viewBox="0 0 8 6"><path d="M1 1l3 3 3-3" stroke="#fff" stroke-width="1.4" fill="none"/></svg></span>
    </nav>
    <form class="abs contact">
      <div class="contact-inner">
        <h2>Contact Us Now<br>For <span class="free">FREE</span></h2>
        <div class="field">Name</div>
        <div class="field">Phone Number</div>
        <div class="field">Email for Reply</div>
        <div class="field area">Tell us about your case</div>
        <div class="send">Click for Contact</div>
      </div>
    </form>
  </section>

  <section class="abs col welcome">
    <h2>Welcome to our site</h2>
    <div class="welcome-photo" role="img" aria-label="Gavel, scales of justice and an open law book"></div>
    <p class="body-copy">Lorem ipsum dolor sit amet, consectetur adipiscing elit. Fusce accumsan, elit a suscipit sagittis, tortor sapien cursus risus, non rhoncus lectus nunc ac nulla.<br>Aliquam molestie, mi et imperdiet euismod, dui purus auctor tellus, et interdum lacus lectus et ante. Sed accumsan sollicitudin sapien, sit amet adipiscing turpis gravida ac.</p>
    <span class="btn" style="margin-top:12px">Learn More</span>
  </section>

  <section class="abs col practice">
    <h2>Practice Areas</h2>
    <div class="p-list">
      <div class="p-item"><div class="thumb" role="img" aria-label="Person fallen on a floor" style="background:linear-gradient(#e8e8e8,#b8a89a)"></div><h3>Slip and Fall Injury</h3><p>Lorem ipsum dolor sit amet, consectetur adipiscing elit.</p></div>
      <div class="p-item"><div class="thumb" role="img" aria-label="Damaged red car after an accident" style="background:linear-gradient(#9aa3a8,#c0282c)"></div><h3>Auto Accident</h3><p>Lorem ipsum dolor sit amet, consectetur adipiscing elit.</p></div>
      <div class="p-item"><div class="thumb" role="img" aria-label="Dog biting a hand" style="background:linear-gradient(#2e4a2a,#8a6a48)"></div><h3>Dog Bite Injury</h3><p>Lorem ipsum dolor sit amet, consectetur adipiscing elit.</p></div>
    </div>
    <span class="btn" style="margin-top:8px">Learn More</span>
  </section>

  <section class="abs col questions">
    <h2 class="alert">Top 10 questions</h2>
    <div style="margin-top:8px">
      <div class="q-item"><div class="video" role="img" aria-label="Video of attorneys answering a question"><svg class="abs" style="left:26px;top:19px" width="10" height="10" viewBox="0 0 10 10"><path d="M2 1l7 4-7 4z" fill="#fff"/></svg></div><h3>Sed ut perspiciatis unde omnis iste natus error?</h3><p>Lorem ipsum dolor sit amet, consectetur adipiscing elit.</p><span class="more">more...</span></div>
      <div class="q-item"><div class="video" role="img" aria-label="Video of attorneys answering a question"><svg class="abs" style="left:26px;top:19px" width="10" height="10" viewBox="0 0 10 10"><path d="M2 1l7 4-7 4z" fill="#fff"/></svg></div><h3>Sed ut perspiciatis unde omnis iste natus error?</h3><p>Lorem ipsum dolor sit amet, consectetur adipiscing elit.</p><span class="more">more...</span></div>
      <div class="q-item"><div class="video" role="img" aria-label="Video of attorneys answering a question"><svg class="abs" style="left:26px;top:19px" width="10" height="10" viewBox="0 0 10 10"><path d="M2 1l7 4-7 4z" fill="#fff"/></svg></div><h3>Sed ut perspiciatis unde omnis iste natus error?</h3><p>Lorem ipsum dolor sit amet, consectetur adipiscing elit.</p><span class="more">more...</span></div>
    </div>
  </section>

  <section class="abs info">
    <section><h3 class="lead">Our Purpose</h3><p>Lorem Ipsum is simply dummy text of the printing and typesetting industry. Lorem Ipsum has been the industry's standard dummy text</p><span class="read">Read More &gt;&gt;</span></section>
    <section><h3>What an Attorney Does</h3><p>Lorem Ipsum is simply dummy text of the printing and typesetting industry. Lorem Ipsum has been the industry's standard dummy text</p><span class="read">Read More &gt;&gt;</span></section>
    <section><h3>Why Choose Us</h3><p>Lorem Ipsum is simply dummy text of the printing and typesetting industry. Lorem Ipsum has been the industry's standard dummy text</p><span class="read">Read More &gt;&gt;</span></section>
  </section>

  <footer class="abs footer">
    <div class="abs member">
      <h2>Membership &amp; Accreditation</h2>
      <svg class="arrows" width="28" height="12" viewBox="0 0 28 12"><path d="M6 1L1 6l5 5M22 1l5 5-5 5" stroke="#999" stroke-width="1.6" fill="none"/></svg>
      <div class="m-item"><div class="badge"></div><p>Lorem ipsum dolor sit amet, consectetur adipiscing elit. Fusce accumsan, elit a suscipit sagittis, tortor sapien cursus risus, non rhoncus lectus nunc ac nulla.</p><span class="btn">Learn More</span></div>
      <div class="m-item"><div class="badge"></div><p>Lorem ipsum dolor sit amet, consectetur adipiscing elit. Fusce accumsan, elit a suscipit sagittis, tortor sapien cursus risus, non rhoncus lectus nunc ac nulla.</p><span class="btn">Learn More</span></div>
    </div>
    <div class="abs office">
      <h2>Main Office</h2>
      <div class="brand-name"><span class="main">Quillbrook</span><span class="sub">Attorneys</span></div>
      <p style="line-height:12px;margin:4px 0 4px">412 Fenwick<br>Lane, Ashbury, K17 3LQ.</p>
      <div class="row"><span>Toll - Free:</span><span>+1 800 xxx xxxx</span></div>
      <div class="row"><span>Telephone:</span><span>+1 800 xxx xxxx</span></div>
      <div>Email : <a href="#">hello@quillbrooklaw.com</a></div>
      <h3>Office Hours:</h3>
      <div>8:30 a.m. to 5:30 p.m.</div>
      <div>(Pacific), M-F</div>
    </div>
    <div class="abs connect">
      <h2>Connect with Us</h2>
      <ul>
        <li><span class="sq"></span>Chatterly</li>
        <li><span class="sq"></span>Friendsfold</li>
        <li><span class="sq"></span>Circlespace</li>
        <li><span class="sq"></span>ClipStream</li>
      </ul>
    </div>
    <div class="abs copyright">Copyright © 2012, Quillbrook.<br>All Rights Reserved. | Legal &nbsp;| &nbsp;Privacy Policy</div>
  </footer>

</div>
</body>
</html>
```